Northfield Builders Guild Business card

We are looking for a new business card design with photo included.
Our business is a nonprofit construction contractor membership organization. We offer business education, assist with business setup and licensing, provide safety training, and provide a member directory.
URL: www.builderslinkguild.org
Color code:
CMYK: 0 cyan, 42 magenta, 100 yellow, 0 black for Print.
Hexidecimal: #FF9900
RGB: R 255; G 153; B 0

```html
<!DOCTYPE html>
<html lang="en">
<head>
<meta charset="utf-8">
<title>Northfield Builders Guild – Business Card</title>
<link href="https://fonts.googleapis.com/css2?family=Montserrat:wght@400;500;600;800&display=swap" rel="stylesheet">
<style>
  :root {
    --page: #141414;
    --card: #2e2e2e;
    --band-grey: #4a4a4a;
    --accent: #f7a823;
    --text-light: #e6e6e6;
    --text-muted: #9a9a9a;
  }
  * { margin: 0; padding: 0; box-sizing: border-box; }
  html, body { width: 1200px; height: 900px; overflow: hidden; }
  body {
    background: var(--page);
    font-family: "Montserrat", sans-serif;
    display: flex; flex-direction: column; align-items: center; justify-content: center;
    gap: 40px;
  }
  .card {
    position: relative; width: 700px; height: 400px;
    background: var(--card); overflow: hidden;
    box-shadow: 0 18px 40px rgba(0,0,0,.6);
  }
  .card svg.frame { position: absolute; inset: 0; }

  /* front */
  .scene-photo {
    position: absolute; left: 200px; top: 60px; width: 500px; height: 340px;
    background: radial-gradient(ellipse at 55% 55%, rgba(120,120,120,.35), rgba(46,46,46,0) 70%);
  }
  .portrait {
    position: absolute; left: 236px; top: 30px; width: 170px; height: 124px;
    border: 4px solid var(--accent); border-radius: 10px;
    background: linear-gradient(180deg, #3c3c3c 0%, #4a5560 60%, #8fb0cc 100%);
  }
  .person { position: absolute; left: 94px; top: 178px; }
  .person-name { color: var(--text-light); font-weight: 600; font-size: 24px; letter-spacing: .5px; }
  .person-role { color: var(--accent); font-weight: 400; font-size: 16px; margin-top: 2px; }

  .brand { position: absolute; right: 60px; top: 170px; text-align: left; }
  .brand-name {
    color: var(--accent); font-weight: 800; font-size: 28px; line-height: 1.05;
    text-transform: uppercase; letter-spacing: .5px; white-space: nowrap;
  }
  .contact {
    position: absolute; left: 400px; top: 242px;
    color: var(--text-light); font-size: 14px; line-height: 1.4;
  }
  .contact .address { color: var(--accent); margin-top: 6px; }

  /* back */
  .back .brand { left: 0; right: 0; top: 110px; text-align: center; }
  .back .brand-name { font-size: 46px; }
  .tagline {
    position: absolute; left: 0; right: 0; top: 250px; text-align: center;
    color: var(--text-muted); font-size: 14px; letter-spacing: .5px;
  }
</style>
</head>
<body>

<section class="card front" aria-label="Business card front">
  <div class="scene-photo" role="img" aria-label="Faint background photo of a contractor's hands holding plans"></div>
  <svg class="frame" width="700" height="400" viewBox="0 0 700 400" aria-hidden="true">
    <defs>
      <pattern id="hatch" width="6" height="6" patternUnits="userSpaceOnUse" patternTransform="rotate(35)">
        <line x1="0" y1="0" x2="0" y2="6" stroke="#5a5a5a" stroke-width="2"/>
      </pattern>
    </defs>
    <polygon points="430,0 700,0 700,44 460,44" fill="var(--band-grey)" opacity=".7"/>
    <polygon points="0,176 82,176 62,200 0,200" fill="var(--accent)"/>
    <polygon points="0,258 360,258 330,296 0,296" fill="url(#hatch)"/>
    <polygon points="300,356 700,356 700,400 260,400" fill="var(--accent)"/>
  </svg>
  <div class="portrait" role="img" aria-label="Portrait photo of the managing director"></div>
  <div class="person">
    <p class="person-name">Dan Whitaker</p>
    <p class="person-role">Managing Director</p>
  </div>
  <div class="brand">
    <p class="brand-name">Northfield<br>Builders Guild</p>
  </div>
  <div class="contact">
    <p>(555) 210-3847</p>
    <p>support@nbguild.org</p>
    <p>www.builderslinkguild.org</p>
    <p class="address">Your address here. Street,<br>City, Country</p>
  </div>
</section>

<section class="card back" aria-label="Business card back">
  <svg class="frame" width="700" height="400" viewBox="0 0 700 400" aria-hidden="true">
    <polygon points="0,0 330,0 300,40 0,40" fill="var(--band-grey)" opacity=".7"/>
    <path d="M0 320 C 200 200, 420 380, 700 180" stroke="#383838" stroke-width="2" fill="none"/>
    <polygon points="0,356 420,356 380,400 0,400" fill="var(--accent)"/>
  </svg>
  <div class="brand">
    <p class="brand-name">Northfield<br>Builders Guild</p>
  </div>
  <p class="tagline">Helping You Reduce Risks And Injuries While Improving Profitability</p>
</section>

</body>
</html>
```